Business Card Design

We are a commercial real estate brokerage in San Francisco, leasing office buildings downtown.
I would like a clean, elegant look. Simple but powerful .

Industry/Entity Type

Business

Contact Information for Business Card

Derek Holloway
lic# 07258143
415.555.0172
derek@velt-commercial.example
velt-commercial.example

```html
<!DOCTYPE html>
<html lang="en">
<head>
<meta charset="utf-8">
<title>VELT Commercial — Business Card</title>
<link rel="stylesheet" href="https://fonts.googleapis.com/css2?family=Open+Sans:wght@400;600&display=swap">
<style>
  :root {
    --slate: #7487a6;
    --slate-deep: #6a7d9c;
    --slate-light: #8a9bb6;
    --ink: #2b2b2b;
    --paper: #ffffff;
    --backdrop: #ecebe8;
  }
  * { box-sizing: border-box; margin: 0; padding: 0; }
  html, body {
    width: 1200px; height: 844px; overflow: hidden;
    background: var(--backdrop);
    font-family: "Open Sans", Arial, sans-serif;
  }
  .canvas {
    position: relative; width: 1200px; height: 844px;
  }
  .card {
    position: absolute; top: 273px;
    width: 520px; height: 298px;
    box-shadow: 0 6px 18px rgba(0,0,0,0.18);
    overflow: hidden;
  }
  .card--front { left: 50px; background: var(--paper); }
  .card--back { left: 630px; background: var(--slate); }

  .brand {
    position: absolute; top: 42px; right: 46px;
    display: flex; align-items: center; gap: 14px;
  }
  .brand__mark {
    width: 40px; height: 40px; background: var(--slate);
  }
  .brand__name {
    font-weight: 600; font-size: 30px; line-height: 1;
    color: var(--slate); letter-spacing: 0.5px;
  }

  .contact {
    position: absolute; left: 38px; top: 124px;
  }
  .contact__name {
    font-weight: 600; font-size: 19px; line-height: 26px; color: var(--slate);
    margin-bottom: 8px;
  }
  .contact__list { list-style: none; }
  .contact__item {
    display: flex; align-items: center; gap: 10px;
    font-size: 14.5px; color: var(--ink); line-height: 22px;
  }
  .contact__icon { width: 12px; height: 12px; fill: var(--slate); flex: none; }

  .band {
    position: absolute; left: 0; right: 0; bottom: 0; height: 62px;
    background: var(--slate);
  }
  .band__license {
    position: absolute; left: 300px; top: 10px;
    color: #fff; font-size: 15px; line-height: 20px; letter-spacing: 0.5px;
  }

  .back__scene {
    position: absolute; inset: 0;
    background: linear-gradient(160deg, var(--slate-light) 0%, var(--slate) 55%, var(--slate-deep) 100%);
  }
  .back__name {
    position: absolute; top: 108px; left: 0; right: 0; text-align: center;
    font-weight: 600; font-size: 44px; line-height: 60px; color: #fff; letter-spacing: 1px;
  }
</style>
</head>
<body>
<main class="canvas">
  <section class="card card--front" aria-label="Card front">
    <div class="brand">
      <span class="brand__mark"></span>
      <span class="brand__name">VELT COMMERCIAL</span>
    </div>

    <div class="contact">
      <p class="contact__name">Derek Holloway</p>
      <ul class="contact__list">
        <li class="contact__item">
          <svg class="contact__icon" viewBox="0 0 24 24"><path d="M6.6 10.8a15.1 15.1 0 0 0 6.6 6.6l2.2-2.2a1 1 0 0 1 1-.25 11.4 11.4 0 0 0 3.6.57 1 1 0 0 1 1 1V20a1 1 0 0 1-1 1A17 17 0 0 1 3 4a1 1 0 0 1 1-1h3.5a1 1 0 0 1 1 1c0 1.25.2 2.45.57 3.6a1 1 0 0 1-.25 1z"/></svg>
          415.555.0172
        </li>
        <li class="contact__item">
          <svg class="contact__icon" viewBox="0 0 24 24"><path d="M2 5h20v14H2z M2 5l10 8 10-8" /></svg>
          derek@velt-commercial.example
        </li>
        <li class="contact__item">
          <svg class="contact__icon" viewBox="0 0 24 24"><path d="M10.6 13.4a1 1 0 0 1 0-1.4l3.5-3.5a1 1 0 1 1 1.4 1.4L12 13.4a1 1 0 0 1-1.4 0zM7 21a4 4 0 0 1-2.8-6.8l3-3 1.4 1.4-3 3a2 2 0 0 0 2.8 2.8l3-3 1.4 1.4-3 3A4 4 0 0 1 7 21zm9.8-7.2-1.4-1.4 3-3a2 2 0 0 0-2.8-2.8l-3 3-1.4-1.4 3-3a4 4 0 0 1 5.6 5.6z"/></svg>
          velt-commercial.example
        </li>
      </ul>
    </div>

    <div class="band">
      <span class="band__license">LIC# 07258143</span>
    </div>
  </section>

  <section class="card card--back" aria-label="Card back">
    <div class="back__scene" role="img" aria-label="Blind-embossed illustration of downtown office towers"></div>
    <p class="back__name">VELT COMMERCIAL</p>
  </section>
</main>
</body>
</html>
```